Need Business Card for our Real Estate Business with Sales Executive's Picture

PANTONE 484 C ( RED)

PANTONE 2766 C ( BLUE

Industry/Entity Type

Real Estate

Contact Information for Business Card

Name, Mobile, email, & picture of Person
Agency Phone, address, Web address

Requirements
Must have
• Our Logo Colours, Agent Picture,

```html
<!DOCTYPE html>
<html lang="en">
<head>
<meta charset="utf-8">
<title>Dunvale Real Estate – Business Card</title>
<link href="https://fonts.googleapis.com/css2?family=Open+Sans:wght@400;600&display=swap" rel="stylesheet">
<style>
  :root {
    --brand-blue: #18275c;
    --brand-red: #b23a2a;
    --paper: #ffffff;
    --backdrop: #d9d9d9;
    --photo-light: #e8ecf3;
    --photo-dark: #2c4480;
  }
  * { box-sizing: border-box; margin: 0; padding: 0; }
  html, body { width: 1200px; height: 852px; overflow: hidden; }
  body {
    background: var(--backdrop);
    font-family: "Open Sans", Arial, sans-serif;
    position: relative;
  }
  .card {
    position: absolute;
    width: 500px;
    height: 286px;
    border-radius: 18px;
    overflow: hidden;
    top: 283px;
  }
  .card--back { left: 70px; background: var(--brand-blue); color: var(--paper); }
  .card--front { left: 630px; background: var(--paper); }

  /* back side */
  .back-brand {
    position: absolute; left: 0; right: 0; top: 100px;
    display: flex; align-items: center; justify-content: center; gap: 10px;
    font-weight: 600; font-size: 34px; letter-spacing: 1px;
  }
  .brand-mark { width: 12px; height: 12px; background: var(--brand-red); flex: none; }
  .back-web {
    position: absolute; left: 0; right: 0; top: 220px;
    display: flex; align-items: center; justify-content: center; gap: 14px;
    font-size: 13px;
  }
  .back-web .rule { width: 50px; height: 2px; background: var(--brand-red); }

  /* front side */
  .front-shape { position: absolute; inset: 0; }
  .front-brand {
    position: absolute; left: 200px; top: 30px;
    display: flex; align-items: center; gap: 8px;
    color: var(--brand-blue); font-weight: 600; font-size: 22px;
  }
  .front-brand .brand-mark { width: 8px; height: 8px; }
  .agent-photo {
    position: absolute; right: 0; bottom: 0; width: 160px; height: 200px;
    background: linear-gradient(180deg, var(--photo-light) 0%, var(--photo-light) 40%, var(--photo-dark) 100%);
  }
  .agent {
    position: absolute; left: 24px; top: 108px; color: var(--paper);
  }
  .agent-name { font-weight: 600; font-size: 17px; }
  .agent-title { font-size: 12px; }
  .contact-list {
    position: absolute; left: 24px; top: 178px; list-style: none;
    color: var(--paper); font-size: 12px; line-height: 17px;
  }
  .contact-list li { display: flex; align-items: center; gap: 8px; }
  .contact-list svg { width: 10px; height: 10px; fill: var(--brand-red); flex: none; }
  .contact-list .no-icon { padding-left: 18px; }
</style>
</head>
<body>

<section class="card card--back" aria-label="Card back">
  <div class="back-brand"><span class="brand-mark"></span>Dunvale Real Estate</div>
  <div class="back-web"><span class="rule"></span>www.dunvalerealestate.com<span class="rule"></span></div>
</section>

<section class="card card--front" aria-label="Card front">
  <svg class="front-shape" viewBox="0 0 500 286" preserveAspectRatio="none">
    <polygon points="0,0 170,0 350,286 0,286" fill="var(--brand-blue)"/>
  </svg>
  <div class="front-brand"><span class="brand-mark"></span>Dunvale Real Estate</div>
  <div class="agent-photo" role="img" aria-label="Portrait photo of the agent in a navy suit"></div>

  <div class="agent">
    <p class="agent-name">Diane Hollis</p>
    <p class="agent-title">Managing Director</p>
  </div>

  <ul class="contact-list">
    <li><svg viewBox="0 0 10 10"><path d="M2 0h2l1 3-1.5 1a6 6 0 0 0 2.5 2.5L7 5l3 1v2a2 2 0 0 1-2 2A8 8 0 0 1 0 2a2 2 0 0 1 2-2z"/></svg>555.210.4837</li>
    <li><svg viewBox="0 0 10 10"><rect x="2" y="0" width="6" height="10" rx="1"/></svg>555-318-2264</li>
    <li><svg viewBox="0 0 10 10"><path d="M0 2h10v6H0z M0 2l5 3.5L10 2" stroke="var(--brand-blue)" stroke-width="0.8"/></svg>dhollis@dunvalerealestate.com</li>
    <li><svg viewBox="0 0 10 10"><circle cx="5" cy="5" r="5"/></svg>www.dunvalerealestate.com</li>
    <li><svg viewBox="0 0 10 10"><path d="M5 0a3.5 3.5 0 0 1 3.5 3.5C8.5 6 5 10 5 10S1.5 6 1.5 3.5A3.5 3.5 0 0 1 5 0z"/></svg>48 Alder Street #210,</li>
    <li class="no-icon">Fairview, CO 80000</li>
  </ul>
</section>

</body>
</html>
```